Dunmore Roofing

Want a professional looking business card

Industry/Entity Type

Business

Contact Information for Business Card

Paul Dunmore ( Owner) paul@dunmoreroofing-example.com, www.dunmoreroofing-example.com, Adress: 4172 Township road 43 Larkfield,MB K9X4T2

```html
<!DOCTYPE html>
<html lang="en">
<head>
<meta charset="utf-8">
<title>Dunmore Roofing – Business Card</title>
<link href="https://fonts.googleapis.com/css2?family=Open+Sans:ital,wght@0,400;0,600;0,700;1,700&display=swap" rel="stylesheet">
<style>
  :root {
    --backdrop: #3b3c3e;
    --brand-blue: #1d4a8e;
    --grey-dark: #6f7072;
    --grey-mid: #8d8e90;
    --text-grey: #6b6c6e;
    --white: #ffffff;
  }
  * { box-sizing: border-box; margin: 0; padding: 0; }
  html, body {
    width: 1200px; height: 900px; overflow: hidden;
    background: var(--backdrop);
    font-family: "Open Sans", Arial, sans-serif;
  }
  .canvas {
    position: relative; width: 1200px; height: 900px;
    display: flex; align-items: center; justify-content: center; gap: 40px;
  }
  .card {
    position: relative; width: 540px; height: 310px; overflow: hidden;
    box-shadow: 0 14px 30px rgba(0,0,0,.45);
  }
  .card--front { background: var(--white); }
  .card__shapes { position: absolute; inset: 0; }
  .contact { position: absolute; left: 34px; top: 30px; color: var(--text-grey); }
  .contact__name {
    color: var(--brand-blue); font-weight: 700; font-style: italic; font-size: 17px; letter-spacing: -.2px;
  }
  .contact__role { font-size: 13px; margin-top: 1px; }
  .contact__address { font-size: 12.5px; line-height: 1.35; margin-top: 16px; }
  .contact__list { list-style: none; margin-top: 6px; font-size: 12.5px; line-height: 1.45; }
  .contact__list li { display: flex; align-items: center; gap: 7px; }
  .contact__icon { width: 15px; height: 15px; flex: none; }
  .wordmark {
    position: absolute; right: 38px; top: 128px; text-align: right;
    color: var(--brand-blue); font-weight: 700; text-transform: uppercase;
    font-size: 26px; letter-spacing: 3px; line-height: 1.15;
  }
  .card--back { background: var(--brand-blue); color: var(--white); }
  .back__map { position: absolute; left: 150px; top: 18px; width: 370px; height: 270px; }
  .back__wordmark {
    position: absolute; left: 0; right: 0; top: 100px; text-align: center;
    font-weight: 700; text-transform: uppercase; font-size: 30px; letter-spacing: 4px; line-height: 1.15;
  }
  .back__url {
    position: absolute; left: 0; right: 0; top: 232px;
    display: flex; align-items: center; justify-content: center; gap: 12px;
    font-size: 12px; letter-spacing: .4px;
  }
  .back__rule { width: 80px; height: 1px; background: rgba(255,255,255,.6); }
</style>
</head>
<body>
<main class="canvas">
  <section class="card card--front" aria-label="Business card, contact side">
    <svg class="card__shapes" viewBox="0 0 540 310" width="540" height="310" aria-hidden="true">
      <polygon points="0,196 205,196 184,228 0,228" fill="var(--grey-dark)"/>
      <polygon points="70,236 196,236 189,246 63,246" fill="var(--grey-mid)"/>
      <polygon points="150,310 188,252 246,252 330,310" fill="var(--brand-blue)"/>
    </svg>
    <div class="contact">
      <p class="contact__name">Paul Dunmore</p>
      <p class="contact__role">Owner</p>
      <p class="contact__address">4172 Township road 43,<br>Larkfield, MB K9X4T2</p>
      <ul class="contact__list">
        <li>
          <svg class="contact__icon" viewBox="0 0 16 16" aria-hidden="true"><circle cx="8" cy="8" r="8" fill="var(--brand-blue)"/><path d="M5.3 4.2l1.4 1.6-.7 1c.5 1.1 1.3 1.9 2.4 2.4l1-.7 1.6 1.4-.8 1.3c-2.9-.3-5.2-2.6-5.5-5.5z" fill="#fff"/></svg>
          (555) 555-0142
        </li>
        <li>
          <svg class="contact__icon" viewBox="0 0 16 16" aria-hidden="true"><circle cx="8" cy="8" r="8" fill="var(--brand-blue)"/><rect x="4" y="5.2" width="8" height="5.6" fill="#fff"/><path d="M4 5.2l4 3 4-3" stroke="var(--brand-blue)" stroke-width=".9" fill="none"/></svg>
          paul@dunmoreroofing-example.com
        </li>
        <li>
          <svg class="contact__icon" viewBox="0 0 16 16" aria-hidden="true"><circle cx="8" cy="8" r="8" fill="var(--brand-blue)"/><g stroke="#fff" stroke-width=".9" fill="none"><circle cx="8" cy="8" r="4.2"/><ellipse cx="8" cy="8" rx="1.8" ry="4.2"/><path d="M3.8 8h8.4"/></g></svg>
          www.dunmoreroofing-example.com
        </li>
      </ul>
    </div>
    <p class="wordmark">Dunmore<br>Roofing</p>
  </section>

  <section class="card card--back" aria-label="Business card, brand side">
    <div class="back__map" role="img" aria-label="Faint dotted world map decoration"
         style="background: radial-gradient(ellipse at 55% 45%, rgba(255,255,255,.09), rgba(255,255,255,0) 70%);"></div>
    <p class="back__wordmark">Dunmore<br>Roofing</p>
    <p class="back__url"><span class="back__rule"></span>www.dunmoreroofing-example.com<span class="back__rule"></span></p>
  </section>
</main>
</body>
</html>
```